Stationery Design Project

We need a stationery design for our Norwegian trucking company. We have existed for about 15 years and our 12 drivers uses relatively new vehicles to transport goods around in northern Norway. Long distance routes with fresh fish og food transport is our main operations.

We have already made alogo that's printed on our trucks. The logo and a picture of our trucks is attached. I think the logo i crappy, but since its already in use, changing it is not an option in this round. Still using a better colour scheme in the overall stationery and more interesting fonts is possible (altso in the logo).

Company details:
Name: Kjelvraket AS
Organisation nr 873 615 309
Post adress: 8642 Raudvik

I like minimalism and simplicity. I am avalibly for questions in normal GMT working hours either here or on mail: ivar@fjordlast.no

Reason: Hi. Im extending the deadline because I needed some time to find a vector file of our logo. Sorry for the inconvenience

Hi, and thanks for all your interest in the project. Some updates:

-          I have decided to commit to using one of the designs. Some designer will get the payment.

-          I have extended the deadline with 24 hours since I needed some time to find our firms vector logo (a slow Swedish man was holding me up)

-          We will not choose a design before the deadline. No need to rush.

-          We have received a lot of great design and think there is a need to specified the product we want to make:

o   Business Card for all our employers. I just need the design and will duplicate with the correct numbers and name myself. The information on should be: Logo, employer’s name, Phone number, email, website, Postal number and address. Use this as a template: logo, Leif Brattvoll, 47382066, Leif@fjordlast.no,, fjordlast.no, 8642 Raudvik. The order and placement of the information is your creative decision.

o   Stickers to put on the goods we travel. On the sticker the should be the following information: Logo, phone number, Tekst and link: Fraktæ av Kjelvraket. Ke du syns? Fjordlast.no/tilbakemelding (this means: Handled by Kjelvraket. What do you think Fjordlast.no/feedback -à the link will be a feedback form). The placement the information and size is your creative decision with some stings: we have been thinking of using Drukko for printing and see that a size about 6x6 cm, 8x5 or something like that. (with 3000 copies our budget is 200 punds). Any suggestions of other suppliers are welcome. Drukko price calculator http://www.drukkolabelhouse.co.uk/digital-litho-printing/printing-labels-tags/stickers/

o   Letterhead with logo, address, phone number and organizational number.

o   Envelopes with logo,address, phone number and organizational number.

Have a nice day.

 

 

• Using the blue colour in the logo and using a similar graphic approch.

```html
<!DOCTYPE html>
<html lang="no">
<head>
<meta charset="utf-8">
<title>Kjelvraket – klistremerker</title>
<link rel="stylesheet" href="https://fonts.googleapis.com/css2?family=Fira+Sans+Extra+Condensed:wght@600&display=swap">
<style>
  :root {
    --backdrop: #a6a6a6;
    --card: #ffffff;
    --brand-blue: #1b6fae;
    --deep-blue: #233f93;
    --light-blue: #2788b8;
    --ink-grey: #4a4a4a;
    --silver-light: #e6e6e6;
    --silver-dark: #6e6e6e;
  }
  html, body {
    margin: 0;
    padding: 0;
    width: 1200px;
    height: 900px;
    overflow: hidden;
    background: var(--backdrop);
  }
  .sheet {
    position: relative;
    width: 1200px;
    height: 900px;
  }
  .sticker {
    position: absolute;
    background: var(--card);
    border-radius: 19px;
    overflow: hidden;
  }
  .sticker--landscape { left: 157px; top: 330px; width: 511px; height: 367px; }
  .sticker--portrait  { left: 703px; top: 185px; width: 368px; height: 511px; }
  .sticker svg { display: block; }
  .type {
    font-family: "Fira Sans Extra Condensed", "Arial Narrow", sans-serif;
    font-weight: 600;
  }
  .tagline   { fill: var(--brand-blue); }
  .question  { fill: var(--brand-blue); }
  .feedback-link { fill: var(--ink-grey); }
  .call-label, .call-number { fill: #ffffff; }
  .brand-name { fill: var(--brand-blue); }
  .brand-dot  { fill: var(--brand-blue); }
</style>
</head>
<body>
<main class="sheet">

  <!-- Landscape sticker -->
  <section class="sticker sticker--landscape" aria-label="Klistremerke liggende">
    <svg width="511" height="367" viewBox="0 0 511 367">
      <defs>
        <linearGradient id="silverL" x1="1" y1="0" x2="0" y2="1">
          <stop offset="0" stop-color="var(--silver-light)"/>
          <stop offset="1" stop-color="var(--silver-dark)"/>
        </linearGradient>
        <linearGradient id="blueL" x1="1" y1="0" x2="0" y2="1">
          <stop offset="0" stop-color="var(--light-blue)"/>
          <stop offset="1" stop-color="var(--deep-blue)"/>
        </linearGradient>
      </defs>
      <path class="swoosh-silver" d="M111 367 Q 410 300 511 98 L511 367 Z" fill="url(#silverL)"/>
      <path class="swoosh-blue" d="M141 367 Q 430 310 511 164 L511 367 Z" fill="url(#blueL)"/>

      <g class="brand">
        <circle class="brand-dot" cx="44" cy="50" r="12"/>
        <text class="type brand-name" x="64" y="61" font-size="32">Kjelvraket</text>
      </g>

      <text class="type tagline" x="31" y="164" font-size="25">Fraktæ av Kjelvraket.</text>
      <text class="type question" x="29" y="216" font-size="56">Ke du syns?</text>
      <text class="type feedback-link" x="31" y="248" font-size="23">Fjordlast.no/tilbakemelding</text>

      <text class="type call-label" x="484" y="309" font-size="18" text-anchor="end">Call</text>
      <text class="type call-number" x="484" y="351" font-size="36" text-anchor="end">47382066</text>
    </svg>
  </section>

  <!-- Portrait sticker -->
  <section class="sticker sticker--portrait" aria-label="Klistremerke stående">
    <svg width="368" height="511" viewBox="0 0 368 511">
      <defs>
        <linearGradient id="silverP" x1="0" y1="0" x2="1" y2="1">
          <stop offset="0" stop-color="var(--silver-light)"/>
          <stop offset="1" stop-color="var(--silver-dark)"/>
        </linearGradient>
        <linearGradient id="blueP" x1="1" y1="0" x2="0.6" y2="1">
          <stop offset="0" stop-color="var(--light-blue)"/>
          <stop offset="1" stop-color="var(--deep-blue)"/>
        </linearGradient>
      </defs>
      <path class="swoosh-silver" d="M98 0 Q 310 110 368 399 L368 0 Z" fill="url(#silverP)"/>
      <path class="swoosh-blue" d="M167 0 Q 335 120 368 368 L368 0 Z" fill="url(#blueP)"/>

      <text class="type call-label" x="355" y="33" font-size="15" text-anchor="end">Call</text>
      <text class="type call-number" x="355" y="67" font-size="29" text-anchor="end">47382066</text>

      <text class="type tagline" x="27" y="225" font-size="25">Fraktæ av Kjelvraket.</text>
      <text class="type question" x="25" y="279" font-size="56">Ke du syns?</text>
      <text class="type feedback-link" x="27" y="309" font-size="23">Fjordlast.no/tilbakemelding</text>

      <g class="brand">
        <circle class="brand-dot" cx="150" cy="465" r="12"/>
        <text class="type brand-name" x="170" y="476" font-size="32">Kjelvraket</text>
      </g>
    </svg>
  </section>

</main>
</body>
</html>
```